Packaging and labelling for Swiss made Organic CBD Oil

Visit our website www.clearleafmerida.example
We have not put any product on yet as require packaging and label design .
Website will give you a great feel for the company and how we have used
the logo . The Vextora cbd product shown is a company similar to ourselves with similar core values , we liked the clean packaging design they have .

Im happy if you want use the mandala symbol in our logo separate from
KELVORA, to separate and use the mandala symbol as a larger icon than
it appears in our logo
Clean , Pure , organic feel. Like the product to look pharmaceutical and life changing not gimmicky.
Colours to go with or be the same as our logo colours
But not too cold and clinical
Bottle size 84mm x 25mm
Label size 75mm x 30mm
Box 30mm x 30mm x 100mm
6 products
Full Spectrum :
500mg CBD (5%)
1000mg CBD ( 10% )
1500mg CBD (15%)
2000mg CBD ( 20% )
Broad spectrum THC Free
500mg CBD (5%)
Pets
500mg Broad Spectrum THC Free
Updates

Would like the design to be more modern than traditional

LABEL Information Front of Bottle - Logo KELVORA & Mandala - Mandala can be used separately as design symbol Organic Cannabis Oil 1500mg CBD (15%) Ful Spectrum 10ml Back of bottle Ingredients: Organic Cannabis Oil Extract Organic Sunflower Seed Oil THC - 0.2% Certified Swiss Organic Cultivation Shake well before use. Store in a cool , dry place and out of the each of children BOX information Front and rear Logo - KELVORA & Mandala - Mandala can be used separately as a design symbol Organic Cannabis Oil 1500mg CBD (15%) Full Spectrum Sides x 2 This product is a food supplement and is not intended to diagnose, treat, cure or prevent any disease If you are pregnant, lactating or taking any medication consult your health care practitioner Suitable for vegetarians and vegans Ingredients Organic Cannabis Oil extract Organis Sunflower Oil Store in a cool ,dry place, out of the reach of children Recommended Use 1-5 drops ( 1 drop = 7.5mg CBD ) Subject to body weight and personal requirement - visit www.clearleafmerida for more information 100% Natural 100% Organic GMO free 100% Vegan ( symbol with each ) Expiry date see bottle label Cultivated and manufactured in Switzerland

Target Market(s)

age 40 - 80

Font styles to use
Other font styles liked:
• In our website we have used Open Sans for the copy and Lato for headings .

Requirements
Must have
• look like an Industry leader
Kelvora will change the quality of peoples lives and in some cases may
even save lives so want look powerful and credible
Our Mission is - Through Delivering Pure , Premium , Organic products we will educate, inform and help people achieve healthier , happier lifestyles
Nice to have
• Colours to look good with our logo colours or be the same as our logo
colours
Logo Font - Avenir Black and Avenir Book

Font used in website - Content - Open Sans / Headings - Lato
If you have another font for the packaging information that will go well with
our logo, I'm happy for you to use your skills

```html
<!DOCTYPE html>
<html lang="en">
<head>
<meta charset="utf-8">
<title>Kelvora Organic CBD Oil – Bottle Label</title>
<link rel="stylesheet" href="https://fonts.googleapis.com/css2?family=Montserrat:wght@300;400;600;700;800&display=swap">
<style>
  :root {
    --page-bg: #ffffff;
    --label-black: #050505;
    --orb-grey: #2a2a2a;
    --brand-white: #ffffff;
    --oil-grey: #dcdcdc;
    --thc-grey: #8a8a8a;
    --organic-green: #6cb35a;
    --ink-dark: #1a1a1a;
    --volume-teal: #9fdad7;
    --mark-teal: #8fd3cf;
  }
  * { margin: 0; padding: 0; box-sizing: border-box; }
  html, body {
    width: 1200px; height: 1000px; overflow: hidden;
    background: var(--page-bg);
    font-family: "Montserrat", sans-serif;
  }
  .label {
    position: absolute; left: 100px; top: 159px;
    width: 1000px; height: 682px;
    background: var(--label-black);
    overflow: hidden;
  }
  .label-backdrop { position: absolute; inset: 0; }
  .brand {
    position: absolute; left: 334px; top: 64px;
    display: flex; align-items: center; gap: 14px;
  }
  .brand-dot {
    width: 26px; height: 26px; border-radius: 50%;
    border: 2px solid var(--mark-teal);
  }
  .brand-name {
    color: var(--brand-white); font-weight: 700;
    font-size: 54px; letter-spacing: 5px; line-height: 1;
  }
  .organic-tag {
    position: absolute; left: 334px; top: 202px;
    width: 288px; height: 46px;
    background: var(--organic-green);
    color: var(--ink-dark); font-weight: 700;
    font-size: 38px; letter-spacing: 9.5px; line-height: 46px;
    padding-left: 6px;
  }
  .product-name {
    position: absolute; left: 332px; top: 248px;
    color: var(--oil-grey); font-weight: 600;
    font-size: 70px; letter-spacing: -1px; line-height: 1.1;
  }
  .thc-free {
    position: absolute; left: 336px; top: 318px;
    color: var(--thc-grey); font-weight: 800;
    font-size: 42px; letter-spacing: 9px; line-height: 1.1;
  }
  .strength {
    position: absolute; left: 334px; top: 440px;
    color: var(--brand-white); font-weight: 300;
    font-size: 64px; line-height: 1.02; text-align: center;
  }
  .volume-tag {
    position: absolute; left: 337px; top: 621px;
    width: 288px; height: 61px;
    background: var(--volume-teal);
    color: var(--ink-dark); font-weight: 700;
    font-size: 38px; letter-spacing: -1px;
    line-height: 61px; text-align: center;
  }
</style>
</head>
<body>
  <section class="label" aria-label="Kelvora organic CBD oil bottle label">
    <svg class="label-backdrop" width="1000" height="682" viewBox="0 0 1000 682"
         role="img" aria-label="Soft dark translucent spheres drifting across a black background">
      <defs>
        <radialGradient id="orb-glow" cx="50%" cy="40%" r="65%">
          <stop offset="0%" stop-color="#1e1e1e"/>
          <stop offset="100%" stop-color="#050505"/>
        </radialGradient>
      </defs>
      <rect width="1000" height="682" fill="url(#orb-glow)"/>
    </svg>

    <div class="brand">
      <span class="brand-dot"></span>
      <span class="brand-name">KELVORA</span>
    </div>

    <div class="organic-tag">ORGANIC</div>
    <h1 class="product-name">CBD OIL</h1>
    <p class="thc-free">THC FREE</p>
    <p class="strength">20% CBD<br>(2000mg)</p>
    <div class="volume-tag">30 ML (1OZ)</div>
  </section>
</body>
</html>
```